Seeking funky, innovative business cards

I am looking to refresh our current business cards to something more engaging, visual and impactful. We are a management consultancy firm, see website (www.larkstone-partners.com.au). I've included our colour scheme, sample of the slides we use and our old business cards. We would like our cards to have icons. The card should display:- Name- Title- Mobile number- Address- Email address- Website - Company logo- Our purpose statement "We create the best places on earth to work"

Contact Information for Business Card

Brennan Ulfsson
Consultant
0468 927 341
Level 3, 218 Wexley Street, Melbourne 3000
brennan@larkstone-partners.com.au
www.larkstone-partners.com.au

Purpose statement "we create the best places on earth to work"
LOGO available in google images

Font styles to use
Other font styles liked:
• Open Sans Light, Bebas Neue (open to other cool foints)

Colors
ffc214
5c5c5c
f5f5f5
fefefe

Requirements
Must have
• - Name
• - Title
• - Mobile number
• - Address
• - Email address
• - Website
• - Company logo
• - Our purpose statement "We create the best places on earth to work"
Nice to have
• - Icons
• - Colour (see our colour scheme"

```html
<!DOCTYPE html>
<html lang="en">
<head>
<meta charset="utf-8">
<title>Larkstone Partners — Business Card</title>
<link rel="stylesheet" href="https://fonts.googleapis.com/css2?family=Bebas+Neue&family=Lato:wght@300;400&display=swap">
<style>
  :root {
    --backdrop: #161616;
    --card: #1f1f1f;
    --card-edge: #262626;
    --accent: #ffd21a;
    --stripe: #f7a823;
    --text: #f5f5f5;
    --muted: #e6e6e6;
  }
  * { box-sizing: border-box; margin: 0; padding: 0; }
  html, body {
    width: 1200px;
    height: 900px;
    overflow: hidden;
    background: radial-gradient(circle at 60% 40%, #2a2a2a 0%, var(--backdrop) 70%);
    font-family: "Lato", sans-serif;
  }
  .canvas { position: relative; width: 1200px; height: 900px; }

  .card {
    position: absolute;
    left: 280px;
    width: 640px;
    height: 366px;
    background: linear-gradient(135deg, var(--card) 0%, var(--card-edge) 60%, var(--card) 100%);
    border-bottom: 5px solid var(--stripe);
    box-shadow: 0 14px 30px rgba(0,0,0,0.55);
  }
  .card--front { top: 62px; }
  .card--back { top: 472px; }

  /* Front */
  .brand {
    position: absolute;
    inset: 0;
    display: flex;
    flex-direction: column;
    align-items: center;
    justify-content: center;
  }
  .brand__row {
    display: flex;
    align-items: center;
    gap: 18px;
  }
  .brand__dot {
    width: 22px; height: 22px;
    border-radius: 50%;
    background: var(--accent);
  }
  .brand__name {
    font-weight: 300;
    font-size: 52px;
    letter-spacing: -0.5px;
    color: var(--text);
    line-height: 1.1;
  }
  .brand__purpose {
    margin-top: 10px;
    font-weight: 400;
    font-size: 13px;
    letter-spacing: 3px;
    text-transform: uppercase;
    color: var(--text);
  }

  /* Back */
  .identity {
    position: absolute;
    right: 340px;
    top: 118px;
    text-align: right;
  }
  .identity__name {
    font-family: "Bebas Neue", sans-serif;
    font-weight: 400;
    font-size: 48px;
    line-height: 1;
    letter-spacing: 1px;
    color: var(--accent);
    white-space: nowrap;
  }
  .identity__title {
    font-size: 18px;
    color: var(--text);
    margin-top: 4px;
  }
  .divider {
    position: absolute;
    left: 318px;
    top: 112px;
    width: 1px;
    height: 98px;
    background: var(--accent);
  }
  .contacts {
    position: absolute;
    left: 340px;
    top: 124px;
    list-style: none;
  }
  .contacts__item {
    display: flex;
    align-items: center;
    gap: 12px;
    height: 25px;
    font-size: 15.5px;
    color: var(--muted);
    white-space: nowrap;
  }
  .contacts__icon { width: 13px; height: 13px; flex: none; }
  .address {
    position: absolute;
    left: 0; right: 0;
    bottom: 26px;
    text-align: center;
    font-size: 17px;
    color: var(--text);
  }
</style>
</head>
<body>
<main class="canvas">

  <section class="card card--front" aria-label="Card front">
    <div class="brand">
      <div class="brand__row">
        <span class="brand__dot"></span>
        <span class="brand__name">Larkstone Partners</span>
      </div>
      <p class="brand__purpose">We create the best places on earth to work</p>
    </div>
  </section>

  <section class="card card--back" aria-label="Card back">
    <div class="identity">
      <h1 class="identity__name">Brennan Ulfsson</h1>
      <p class="identity__title">Consultant</p>
    </div>

    <div class="divider"></div>

    <ul class="contacts">
      <li class="contacts__item">
        <svg class="contacts__icon" viewBox="0 0 16 16" aria-hidden="true"><path d="M4 1.5l2.2 3-1.3 1.5c.8 1.9 2.2 3.4 4.1 4.3l1.5-1.3 3 2.2-1.2 2.6C7 13.5 2.5 9 1.4 2.7z" fill="none" stroke="#ffd21a" stroke-width="1.4" stroke-linejoin="round"/></svg>
        <span>0468 927 341</span>
      </li>
      <li class="contacts__item">
        <svg class="contacts__icon" viewBox="0 0 16 16" aria-hidden="true"><rect x="1.5" y="3.5" width="13" height="9" fill="none" stroke="#ffd21a" stroke-width="1.3"/><path d="M1.5 3.5l6.5 5 6.5-5" fill="none" stroke="#ffd21a" stroke-width="1.3"/></svg>
        <span>brennan@larkstone-partners.com.au</span>
      </li>
      <li class="contacts__item">
        <svg class="contacts__icon" viewBox="0 0 16 16" aria-hidden="true"><g fill="none" stroke="#ffd21a" stroke-width="1.2"><circle cx="8" cy="8" r="6.5"/><ellipse cx="8" cy="8" rx="3" ry="6.5"/><path d="M1.5 8h13M2.5 4.8h11M2.5 11.2h11"/></g></svg>
        <span>www.larkstone-partners.com.au</span>
      </li>
    </ul>

    <p class="address">Level 3, 218 Wexley Street Melbourne, VIC 3000</p>
  </section>

</main>
</body>
</html>
```